HARBORLINE AUTO GLASS

Mobile Glass Shop:

1) Windshield REPAIR 2)Windshield replacment 3) Rear Windshield Replacment 4) Side Window Replacment 5) car window replacment 6) Power Window Repair.

Schedual a service within 24 hour with one of our certified technicians.
Updates

See "brightvane auto repair" web site for referance on the nature of our buisness and service. www.brightvane-example.com

Coding

```html
<!DOCTYPE html>
<html lang="en">
<head>
<meta charset="utf-8">
<title>Harborline Auto Glass</title>
<link href="https://fonts.googleapis.com/css2?family=Roboto+Condensed:wght@400;700&family=Roboto:wght@400;500;700&family=Mulish:wght@400;600&display=swap" rel="stylesheet">
<style>
:root{
  --blue:#2b93d3;
  --blue-deep:#0d5c9c;
  --blue-light:#3cb0e8;
  --ink:#262626;
  --grey-text:#8a8a8a;
  --soft:#f3f3f3;
  --footer:#2e2e2e;
  --white:#fff;
}
*{margin:0;padding:0;box-sizing:border-box}
html,body{width:1200px;height:3705px;overflow:hidden;background:var(--white)}
body{position:relative;font-family:"Roboto",sans-serif;color:var(--ink)}
.abs{position:absolute}
.blue{color:var(--blue)}

/* top bar */
.topbar{left:626px;top:0;width:574px;height:36px;background:#262626;clip-path:polygon(0 0,100% 0,100% 100%,36px 100%)}
.topbar .info{position:absolute;top:10px;font-size:13px;color:#fff;display:flex;align-items:center;gap:8px;white-space:nowrap}
.social{display:flex;gap:6px}
.social span{width:24px;height:24px;border-radius:50%;background:#fff;display:block}
.social span.b{background:var(--blue)}

/* header */
.logo{display:flex;align-items:center;gap:10px}
.logo .mark{width:40px;height:40px;background:var(--blue)}
.logo .name{font-family:"Roboto Condensed",sans-serif;font-weight:700;color:var(--blue);font-size:24px;line-height:1.05;letter-spacing:.5px}
.nav{top:80px;left:417px;display:flex;gap:25px;font-size:14px;font-weight:500}
.nav a{color:var(--ink);text-decoration:none}
.nav a.on{color:var(--blue)}
.btn{display:inline-flex;align-items:center;justify-content:center;background:var(--blue);color:#fff;font-family:"Roboto",sans-serif;font-weight:700;text-transform:uppercase}
.btn-quote{left:946px;top:63px;width:142px;height:50px;font-size:14px}

/* hero */
.hero{left:0;top:143px;width:1200px;height:710px;background:linear-gradient(120deg,#5d7a93 0%,#2c4a66 30%,#8fa2b3 55%,#4a5f72 75%,#1e2e3e 100%)}
.hero-box{left:600px;top:301px;width:488px;height:265px;background:rgba(240,242,245,.9)}
.hero-box h1{position:absolute;left:40px;top:42px;font-family:"Roboto Condensed",sans-serif;font-size:36px;font-weight:700;color:#1f1f1f;white-space:nowrap}
.hero-box p{position:absolute;left:42px;top:92px;width:410px;font-family:"Mulish",sans-serif;font-size:18px;line-height:29px;color:#333}
.hero-box .btn{position:absolute;left:42px;top:169px;width:142px;height:49px;font-size:14px}
.dots{left:564px;top:733px;display:flex;gap:9px}
.dots span{width:10px;height:10px;border:1.5px solid #fff;border-radius:50%}
.dots span.on{background:#fff}

/* section titles */
.title{width:1200px;left:0;text-align:center;font-family:"Roboto Condensed",sans-serif;font-weight:700;font-size:44px;color:var(--ink)}

/* services */
.card{width:309px;height:428px;background:#fff;box-shadow:0 2px 14px rgba(0,0,0,.12);text-align:center}
.card .ph{position:absolute;left:9px;top:9px;width:291px;height:206px}
.card h3{position:absolute;left:0;width:100%;top:234px;font-size:16px;font-weight:500;letter-spacing:.4px}
.card .rule{position:absolute;left:127px;top:263px;width:55px;height:2px;background:var(--blue-deep)}
.card p{position:absolute;left:18px;width:273px;top:278px;font-size:13.5px;line-height:23px;color:var(--grey-text)}
.card .btn{position:absolute;left:106px;top:368px;width:97px;height:34px;font-size:10px}
.card.active{background:linear-gradient(180deg,#3aaae4,#1670b2)}
.card.active h3,.card.active p{color:#fff}
.card.active .rule{background:#fff}
.card.active .btn{background:#fff;color:var(--ink)}

/* about */
.about{left:0;top:1948px;width:1200px;height:499px;background:var(--soft)}
.about .ph{position:absolute;left:0;top:0;width:660px;height:499px;background:linear-gradient(90deg,#4b5b6a 0%,#7d8a95 45%,#b5bcc2 80%,rgba(243,243,243,0) 100%)}
.about h2{position:absolute;left:600px;top:74px;font-family:"Roboto Condensed",sans-serif;font-size:38px;font-weight:700}
.about p{position:absolute;left:600px;top:145px;width:488px;font-size:14px;line-height:26.5px;color:var(--grey-text);text-align:justify}
.about .btn{position:absolute;left:600px;top:366px;width:142px;height:49px;font-size:14px}

/* testimonials */
.quote{width:409px;height:213px;background:#fff;border-radius:38px;box-shadow:0 4px 16px rgba(0,0,0,.13)}
.quote .q{position:absolute;left:80px;top:10px;font-family:"Roboto",sans-serif;font-weight:700;font-size:60px;color:var(--blue);line-height:1}
.quote p{position:absolute;left:82px;top:66px;width:300px;font-size:11px;line-height:21.5px;color:var(--grey-text);text-align:justify}
.quote h4{position:absolute;left:82px;top:144px;font-size:15px;font-weight:500;letter-spacing:.5px}
.quote .stars{position:absolute;left:82px;top:166px;font-size:11px;color:#f2a400;letter-spacing:1px}
.avatar{width:94px;height:94px;border-radius:50%;background:linear-gradient(160deg,#8b9aa7,#4f5d69)}

/* cta */
.cta{left:0;top:2934px;width:1200px;height:360px;background:linear-gradient(160deg,#3db1e7 0%,#2a8fd0 50%,#1a6eb0 100%)}
.cta h2{position:absolute;left:0;width:100%;top:86px;text-align:center;font-family:"Roboto Condensed",sans-serif;font-weight:700;font-size:33px;line-height:50px;color:#fff}
.cta .btn{position:absolute;left:529px;top:213px;width:142px;height:51px;background:#fff;color:var(--ink);font-size:14px;font-weight:500}

/* footer */
.footer{left:0;top:3293px;width:1200px;height:412px;background:var(--footer);color:#fff}
.footer .logo{position:absolute;left:500px;top:62px}
.fnav{position:absolute;left:0;width:100%;top:176px;display:flex;justify-content:center;gap:24px;font-size:15px;font-weight:700}
.fnav i{font-style:normal;font-weight:400}
.hr{position:absolute;left:111px;width:977px;height:1px;background:#4a4a4a}
.vr{position:absolute;top:236px;width:1px;height:104px;background:#4a4a4a}
.ci{position:absolute;top:247px;width:76px;height:76px;border-radius:50%;background:#fff;display:flex;align-items:center;justify-content:center}
.ct{position:absolute;top:263px;font-size:13px;line-height:22px;white-space:nowrap}
.ct b{display:block;font-size:14px}
.copy{position:absolute;left:0;width:100%;top:375px;text-align:center;font-size:11px}
</style>
</head>
<body>

<!-- top bar -->
<div class="abs topbar">
  <div class="info" style="left:60px">
    <svg width="12" height="12" viewBox="0 0 24 24"><path fill="#fff" d="M6.6 10.8a15 15 0 006.6 6.6l2.2-2.2c.3-.3.7-.4 1-.2 1.1.4 2.3.6 3.6.6.6 0 1 .4 1 1V20c0 .6-.4 1-1 1A17 17 0 013 4c0-.6.4-1 1-1h3.5c.6 0 1 .4 1 1 0 1.3.2 2.5.6 3.6.1.3 0 .7-.2 1z"/></svg>
    +1 (555) 014 2290
  </div>
  <div class="info" style="left:213px;color:#aaa">|</div>
  <div class="info" style="left:232px">
    <svg width="13" height="10" viewBox="0 0 26 20"><path fill="#fff" d="M0 0h26v20H0z"/><path fill="#262626" d="M1 1l12 9 12-9v2L13 12 1 3z"/></svg>
    info@hag.example
  </div>
  <div class="social" style="position:absolute;left:378px;top:6px"><span class="b"></span><span></span><span></span></div>
</div>

<!-- header -->
<div class="abs logo" style="left:114px;top:52px">
  <div class="mark"></div>
  <div class="name">HARBORLINE<br>AUTO GLASS</div>
</div>
<nav class="abs nav">
  <a class="on">HOME</a><a>ABOUT US</a><a>OUR SERVICES</a><a>RESOURCES</a><a>CONTACT US</a>
</nav>
<div class="abs btn btn-quote">Get a Quote</div>

<!-- hero -->
<div class="abs hero" role="img" aria-label="Technician in blue cap and uniform fitting a windshield in a workshop"></div>
<div class="abs hero-box">
  <h1>HARBORLINE <span class="blue">AUTO GLASS</span></h1>
  <p>Lorem ipsum dolor sit amet, consectetur adipi scing elit, sed do eiusea.</p>
  <div class="btn">Get Started</div>
</div>
<div class="abs dots"><span></span><span class="on"></span><span></span><span></span></div>
<svg class="abs" style="left:0;top:690px" width="1200" height="165" viewBox="0 0 1200 165">
  <path fill="#fff" d="M0 165V120C300 40 800 20 1200 160V165z"/>
  <path fill="#0d5c9c" d="M0 120C300 40 800 22 1200 150V160C800 40 300 62 0 138z"/>
  <path fill="#0d5c9c" d="M0 138C60 122 120 110 180 104L90 135 232 160H0z"/>
  <path fill="none" stroke="#2b93d3" stroke-width="3" d="M230 102C500 40 900 40 1200 140"/>
</svg>

<!-- services -->
<h2 class="abs title" style="top:870px">OUR <span class="blue">SERVICES</span></h2>

<div class="abs card" style="left:111px;top:960px">
  <div class="ph" role="img" aria-label="Hands lifting a windshield with suction cups" style="background:linear-gradient(135deg,#53636e,#b9c2c8 60%,#7b8790)"></div>
  <h3>WINDSHIELD REPAIR</h3><div class="rule"></div>
  <p>Lorem ipsum dolor sit amet, consecte tur adipiscing elit, sed do eiusmod tempor incidid amet untea.</p>
  <div class="btn">Learn More</div>
</div>
<div class="abs card active" style="left:446px;top:960px">
  <div class="ph" role="img" aria-label="Mechanic working on a windshield with tools in a garage" style="background:linear-gradient(135deg,#cfd3d4,#6f7d77 50%,#3a4a44)"></div>
  <h3>WINDSHIELD REPLACMENT</h3><div class="rule"></div>
  <p>Lorem ipsum dolor sit amet, consecte tur adipiscing elit, sed do eiusmod tempor incidid amet untea.</p>
  <div class="btn">Learn More</div>
</div>
<div class="abs card" style="left:780px;top:960px">
  <div class="ph" role="img" aria-label="Gloved hands working on a rear windshield in warm light" style="background:linear-gradient(135deg,#3a2a22,#a0643a 50%,#2b2220)"></div>
  <h3>REAR WINDSHIELD REPLACMENT</h3><div class="rule"></div>
  <p>Lorem ipsum dolor sit amet, consecte tur adipiscing elit, sed do eiusmod tempor incidid amet untea.</p>
  <div class="btn">Learn More</div>
</div>

<div class="abs card" style="left:111px;top:1412px">
  <div class="ph" role="img" aria-label="Technician fitting a car side window outdoors" style="background:linear-gradient(135deg,#8a9a7a,#4d5a66 55%,#2a3440)"></div>
  <h3>SIDE WINDOW REPLACMENT</h3><div class="rule"></div>
  <p>Lorem ipsum dolor sit amet, consecte tur adipiscing elit, sed do eiusmod tempor incidid amet untea.</p>
  <div class="btn">Learn More</div>
</div>
<div class="abs card" style="left:446px;top:1412px">
  <div class="ph" role="img" aria-label="Gloved hand holding a suction tool on car glass" style="background:linear-gradient(135deg,#2a2e33,#6f767c 50%,#1c1f22)"></div>
  <h3>CAR WINDOW REPLACMENT</h3><div class="rule"></div>
  <p>Lorem ipsum dolor sit amet, consecte tur adipiscing elit, sed do eiusmod tempor incidid amet untea.</p>
  <div class="btn">Learn More</div>
</div>
<div class="abs card" style="left:780px;top:1412px">
  <div class="ph" role="img" aria-label="Worker fitting a power window panel into a car door" style="background:linear-gradient(135deg,#1f3342,#5aa6c8 50%,#2b2f35)"></div>
  <h3>POWER WINDOW REPAIR</h3><div class="rule"></div>
  <p>Lorem ipsum dolor sit amet, consecte tur adipiscing elit, sed do eiusmod tempor incidid amet untea.</p>
  <div class="btn">Learn More</div>
</div>

<!-- about -->
<section class="abs about">
  <div class="ph" role="img" aria-label="Technician in overalls repairing a windshield chip with a tool"></div>
  <h2>ABOUT <span class="blue">US</span></h2>
  <p>Sed ut perspiciatis unde omnis iste natus error sit voluptatem accusantium doloremque laudantium, totam rem aperiam, eaque ipsa quae ab illo inventore veritatis et quasi architecto beatae vitae dicta sunt explicabo. Nemo enim ipsam voluptatem quia voluptas sit aspernatur aut odit aut fugit, sed quia consequuntur magni dolores eos qui ratione voluptatem sequi nesciunt neque porro dolorem ipsum quia dolor sit amveritatis etea consectetur adipisci velit sedea.</p>
  <div class="btn">Learn More</div>
</section>

<!-- testimonials -->
<h2 class="abs title" style="top:2526px;font-size:36px">WHAT OUR <span class="blue">CUSTOMERS SAY</span></h2>

<div class="abs quote" style="left:181px;top:2620px">
  <div class="q">“</div>
  <p>Lorem ipsum dolor sit amet, consectetur adipiscing elit, sed do eiusmod tempor incididunt ut labore et dolore magna aliqua. Ut enim ad minimea.</p>
  <h4>JOHN SMITH</h4><div class="stars">★★★★★</div>
</div>
<div class="abs avatar" style="left:140px;top:2680px" role="img" aria-label="Customer portrait"></div>

<div class="abs quote" style="left:663px;top:2620px">
  <div class="q">“</div>
  <p>Lorem ipsum dolor sit amet, consectetur adipiscing elit, sed do eiusmod tempor incididunt ut labore et dolore magna aliqua. Ut enim ad minimea.</p>
  <h4>JOHN SMITH</h4><div class="stars">★★★★★</div>
</div>
<div class="abs avatar" style="left:622px;top:2680px;background:linear-gradient(160deg,#c9d2d8,#6e7f8c)" role="img" aria-label="Customer portrait"></div>

<!-- call to action -->
<section class="abs cta">
  <h2>SCHEDULE A SERVICE WITHIN 24 HOUR WITH ONE<br>OF OUR CERTIFIED TECHNICIANS</h2>
  <div class="btn">Get a Quote</div>
</section>

<!-- footer -->
<footer class="abs footer">
  <div class="logo"><div class="mark"></div><div class="name">HARBORLINE<br>AUTO GLASS</div></div>
  <div class="fnav"><span>HOME</span><i>|</i><span>ABOUT US</span><i>|</i><span>OUR SERVICES</span><i>|</i><span>RESOURCES</span><i>|</i><span>CONTACT US</span></div>
  <div class="hr" style="top:215px"></div>
  <div class="vr" style="left:424px"></div>
  <div class="vr" style="left:776px"></div>

  <div class="ci" style="left:111px">
    <svg width="34" height="34" viewBox="0 0 24 24"><path fill="none" stroke="#2b93d3" stroke-width="1.8" d="M12 21s-6-6.2-6-11a6 6 0 0112 0c0 4.8-6 11-6 11z"/><circle cx="12" cy="10" r="2.2" fill="#2b93d3"/><ellipse cx="12" cy="21" rx="6" ry="1.6" fill="none" stroke="#2b93d3" stroke-width="1.2"/></svg>
  </div>
  <div class="ct" style="left:210px"><b>LOCATION:</b>212 Quayside Lane, Portland,<br>United States</div>

  <div class="ci" style="left:494px">
    <svg width="32" height="32" viewBox="0 0 24 24"><path fill="#2b93d3" d="M6.6 10.8a15 15 0 006.6 6.6l2.2-2.2c.3-.3.7-.4 1-.2 1.1.4 2.3.6 3.6.6.6 0 1 .4 1 1V20c0 .6-.4 1-1 1A17 17 0 013 4c0-.6.4-1 1-1h3.5c.6 0 1 .4 1 1 0 1.3.2 2.5.6 3.6.1.3 0 .7-.2 1z"/></svg>
  </div>
  <div class="ct" style="left:594px"><b>PHONE:</b>+1 (555) 014 2290</div>

  <div class="ci" style="left:900px">
    <svg width="36" height="30" viewBox="0 0 26 20"><rect x="1" y="4" width="24" height="15" fill="none" stroke="#2b93d3" stroke-width="1.6"/><path d="M1 4l12 9 12-9" fill="none" stroke="#2b93d3" stroke-width="1.6"/></svg>
  </div>
  <div class="ct" style="left:1001px"><b>EMAIL:</b>info@hag.example</div>

  <div class="hr" style="top:358px"></div>
  <div class="copy">© 2022 <b>HARBORLINE AUTO GLASS</b> &nbsp;|&nbsp; All Rights Reserved</div>
  <div class="social" style="position:absolute;left:977px;top:369px"><span class="b" style="width:33px;height:33px"></span><span style="width:33px;height:33px"></span><span style="width:33px;height:33px"></span></div>
</footer>

</body>
</html>
```